Quorva - corporate Business Card

We need a good look and innovative business card for a new start up company based in Los Angeles called "Quorva". We are in a payment business, including payment card, app, and ewallet. We are expert in online payment and Card not present (CNP) transaction.
We need an innovative, modern business card.

Our logo font is Aero Matics

Target Market(s)

Startup - Bank - Online Payment - Card Manufacturing

Industry/Entity Type

Startup

Contact Information for Business Card

phone: 555 014 7396 - Address: 4172 Marlowe blvd, Ravenna Park, CA 90299

Requirements
Must have
• Message: innovative, professional, expert, high tech, trust, online payment expert, security
Nice to have
• no comment
Should not have
• no Comment

```html
<!DOCTYPE html>
<html lang="en">
<head>
<meta charset="utf-8">
<title>Quorva – Business Card</title>
<link rel="stylesheet" href="https://fonts.googleapis.com/css2?family=Open+Sans:wght@400;600;700&display=swap">
<style>
  :root {
    --brand-red: #b71f2f;
    --card-white: #ffffff;
    --page-bg: #e8e4df;
    --ink-grey: #555555;
    --shadow: rgba(0, 0, 0, 0.18);
  }
  * { margin: 0; padding: 0; box-sizing: border-box; }
  html, body {
    width: 1200px;
    height: 987px;
    overflow: hidden;
    background: var(--page-bg);
    font-family: "Open Sans", Arial, sans-serif;
  }
  .card {
    position: absolute;
    left: 292px;
    width: 616px;
    height: 352px;
    background: var(--card-white);
    box-shadow: 0 2px 8px var(--shadow);
    overflow: hidden;
  }
  .card--front { top: 130px; }
  .card--back { top: 505px; }

  .front-band {
    position: absolute;
    inset: 0;
    width: 616px;
    height: 352px;
  }
  .front-band path { fill: var(--brand-red); }

  .contact-block {
    position: absolute;
    left: 36px;
    top: 0;
    color: var(--card-white);
  }
  .holder-name {
    position: absolute;
    top: 74px;
    left: 0;
    font-size: 20px;
    font-weight: 600;
    white-space: nowrap;
    letter-spacing: 0.2px;
  }
  .holder-role {
    position: absolute;
    top: 102px;
    left: 0;
    font-size: 16px;
    white-space: nowrap;
  }
  .address {
    position: absolute;
    top: 150px;
    left: 0;
    font-size: 15.5px;
    line-height: 23px;
    font-style: normal;
    white-space: nowrap;
  }
  .contact-list {
    position: absolute;
    top: 207px;
    left: 0;
    list-style: none;
    font-size: 15.5px;
    line-height: 23.5px;
    white-space: nowrap;
  }
  .contact-list li {
    display: flex;
    align-items: center;
  }
  .contact-icon {
    width: 14px;
    height: 14px;
    margin-right: 11px;
    fill: var(--card-white);
  }

  .brand-lockup {
    position: absolute;
    left: 117px;
    top: 118px;
    display: flex;
    align-items: center;
  }
  .brand-dot {
    width: 116px;
    height: 116px;
    border-radius: 50%;
    background: var(--brand-red);
    margin-right: 14px;
  }
  .brand-name {
    font-size: 70px;
    font-weight: 600;
    color: var(--brand-red);
    line-height: 1;
    letter-spacing: 1px;
  }
  .back-url {
    position: absolute;
    left: 0;
    right: 0;
    top: 291px;
    text-align: center;
    font-size: 15px;
    letter-spacing: 7px;
    color: var(--ink-grey);
  }
</style>
</head>
<body>

<section class="card card--front" aria-label="Business card front">
  <svg class="front-band" viewBox="0 0 616 352" aria-hidden="true">
    <path d="M0 0 H440 A176 176 0 0 1 440 352 H0 Z"/>
  </svg>

  <div class="contact-block">
    <h1 class="holder-name">DANA WHITLOCK</h1>
    <p class="holder-role">CEO&amp;Founder</p>
    <address class="address">
      4172 Marlowe blvd<br>
      Ravenna Park, CA 90299
    </address>
    <ul class="contact-list">
      <li>
        <svg class="contact-icon" viewBox="0 0 16 16" aria-hidden="true">
          <path d="M3.2 1 L6 1.6 L6.8 5 L5 6.4 C5.9 8.3 7.6 10 9.6 11 L11 9.2 L14.4 10 L15 12.8 C15 14 14 15 12.8 15 C6.4 15 1 9.6 1 3.2 C1 2 2 1 3.2 1 Z"/>
        </svg>
        555 014 7396
      </li>
      <li>
        <svg class="contact-icon" viewBox="0 0 16 16" aria-hidden="true">
          <path d="M1 3.5 H15 V12.5 H1 Z M2.2 4.5 L8 8.8 L13.8 4.5 Z" fill-rule="evenodd"/>
        </svg>
        dana@quorva.com
      </li>
      <li>
        <svg class="contact-icon" viewBox="0 0 16 16" aria-hidden="true">
          <circle cx="8" cy="8" r="7"/>
          <path d="M4 4.5 C5.5 5 6 6 5.5 7.5 C5 9 6.5 9.5 7 11 L6.5 13.5 C4 12.5 2.6 10 3 7 Z M9.5 3 C11 3.5 12 4.5 12.5 6 L10.5 7 C9.5 6.5 9 5 9.5 3 Z M10 9 L12.8 9.5 C12.3 11.3 11 12.7 9.5 13.3 C9.3 11.8 9.5 10.3 10 9 Z" fill="#b71f2f"/>
        </svg>
        www.quorva.com
      </li>
    </ul>
  </div>
</section>

<section class="card card--back" aria-label="Business card back">
  <div class="brand-lockup">
    <span class="brand-dot" aria-hidden="true"></span>
    <span class="brand-name">Quorva</span>
  </div>
  <p class="back-url">www.quorva.com</p>
</section>

</body>
</html>
```